NexaBRIDGE new era @ Hyper Digitalization

We need a Brochure that show all our product, services and consulting related to Hyper Digitalization into the industrial internet of things world.
We need a document that can be handled as a electronic brochure, this means that we need to show strong corporate presence, with strong skill of technology, and we have credentials and key sucess projects related to Manufacturing industries.
Key industries that we attend: Automotive, Chemical, Food and Beverage, Mining, Paper and Pulp, Oil and Gas, Energy Management.
We save money to our customer in 6 ways: 1) Eficiency in operation 2) Production Control 3) Hyper Digitalization of Thing Optimizing asset ussage 4) Maintenance and predictive of assets risks 5) Quality Control reducing Cost 6) Augmented Reality in operation and control
Target Market(s)
Manufacturing Industry. CEO of companies that has challenges of saving operation costs into plants of manufacturing.
Industry/Entity Type
Software
Other font styles liked:
- MONTSERRAT
Requirements
Must have
- Technology Enviroment, our logo, our expertise, simple message about what our company does and the DNA, infography of the company, cases of sucess, cases of savings $ using our tecnology and services, what we can do for the customer in a few words
Nice to have
- standarize our colors related to our presentation, futuristic, information related to Artificial Inteligence related to machinery
Should not have
- old version of technology,

```html
<!DOCTYPE html>
<html lang="en">
<head>
<meta charset="utf-8">
<title>NexaBRIDGE Brochure Pages</title>
<link href="https://fonts.googleapis.com/css2?family=Montserrat:wght@400;500;600;700;800&display=swap" rel="stylesheet">
<style>
:root{
  --board:#dcdcdc;
  --ink:#1f2226;
  --blue:#1a76c2;
  --blue-deep:#1d4fb0;
  --blue-light:#8fc3f0;
  --grey:#7b8088;
  --arc-grey:#8e949b;
  --navy:#2e3370;
  --navy-dark:#1c2550;
  --dna:#4a5bd6;
  --white:#ffffff;
}
*{box-sizing:border-box;margin:0;padding:0}
html,body{width:1200px;height:1144px;overflow:hidden;background:var(--board)}
body{position:relative;font-family:'Montserrat',sans-serif;color:var(--ink)}
.page{position:absolute;width:883px;height:497px;transform:scale(.6098);transform-origin:0 0;overflow:hidden}
.page-label{position:absolute;font-size:14px;font-weight:400;color:var(--ink)}
.abs{position:absolute}
.brand{position:absolute;font-size:20px;font-weight:600;letter-spacing:.5px}
.url{position:absolute;font-size:10px;letter-spacing:3px}
.ticks{list-style:none}
.ticks li{position:relative;padding-left:22px}
.ticks li::before{content:"";position:absolute;left:0;top:2px;width:9px;height:9px;border:1.3px solid currentColor;border-radius:50%}
.ticks li::after{content:"";position:absolute;left:3px;top:4px;width:3px;height:5px;border:solid currentColor;border-width:0 1.3px 1.3px 0;transform:rotate(40deg)}
.dots{list-style:none}
.dots li{position:relative;padding-left:20px}
.dots li::before{content:"";position:absolute;left:2px;top:4px;width:5px;height:5px;border-radius:50%;background:var(--blue)}

/* page 1 */
.p1{left:55.5px;top:52px;background:radial-gradient(circle at 25% 40%,#2a63c7,#1846a3 70%)}
.p1 .brand{left:44px;top:45px;font-size:46px;color:var(--blue-light);font-weight:500}
.p1 .tagline{left:44px;top:155px;color:var(--white);font-size:18px;line-height:24px}
.p1 .tagline strong{font-weight:600}
.p1 .ticks{left:46px;top:243px;color:var(--white);font-size:11.5px}
.p1 .ticks li{margin-bottom:12px}
.p1 .year{left:42px;top:375px;font-size:56px;font-weight:800;letter-spacing:8px;color:#3f68bd}
.p1 .rule{left:44px;top:440px;width:210px;height:1px;background:#8aa6de}
.p1 .url{left:44px;top:450px;color:var(--white);font-size:12px}

/* page 2 */
.p2{left:619.5px;top:52px;background:linear-gradient(135deg,#ffffff,#eef0f2)}
.p2 .brand{left:28px;top:30px;color:var(--blue)}
.p2 .lead{left:28px;top:80px;width:395px;font-size:16.5px;line-height:23px;font-weight:700;color:var(--blue)}
.p2 .dots{left:28px;top:207px;width:320px;font-size:9px;line-height:13px;letter-spacing:-.1px}
.p2 .dots li{margin-bottom:9px}
.p2 .key{left:485px;top:25px;font-size:50px;font-weight:800;color:#3c8fab;opacity:.85;white-space:nowrap}
.p2 .url{left:30px;top:455px;color:#333}

/* page 3 */
.p3{left:55.5px;top:416.5px;background:linear-gradient(180deg,#cfc6c9 0%,#e6cfb8 35%,#b49f98 62%,#5b4f5a 100%)}
.p3 .brand{left:28px;top:30px;color:var(--white)}
.card{position:absolute;top:78px;height:202px;width:381px;border:1px solid rgba(60,60,70,.45);border-radius:16px;background:rgba(255,255,255,.12)}
.card-head{height:36px;border-radius:14px 14px 6px 6px;color:var(--white);font-size:18px;font-weight:700;text-align:center;line-height:36px;box-shadow:0 3px 4px rgba(0,0,0,.25)}
.themes{left:42px}
.themes .card-head{background:linear-gradient(180deg,#2c8ed3,#0d5a9c)}
.terms{left:450px}
.terms .card-head{background:linear-gradient(180deg,#4a4a4e,#1b1b1e)}
.card .ticks{margin:20px 20px 0 24px;font-size:10.2px;line-height:13px;color:#2a2a30}
.themes .ticks li{margin-bottom:14px}
.terms .ticks{margin-top:14px}
.terms .ticks li{margin-bottom:7px}
.p3 .url{left:32px;top:452px;color:var(--white)}

/* page 4 */
.p4{left:619.5px;top:416.5px;background:radial-gradient(circle at 78% 30%,#3a3e6e,#2a2140 55%,#1f1424)}
.p4 .strip{left:0;top:0;width:47px;height:497px;background:var(--navy-dark)}
.p4 .panel{left:47px;top:0;width:293px;height:497px;background:var(--navy)}
.p4 .brand{left:0;width:387px;text-align:center;top:30px;color:#5aa2e8}
.p4 h2{position:absolute;left:47px;width:293px;text-align:center;top:82px;font-size:44px;font-weight:800;color:var(--dna)}
.p4 .intro{left:64px;top:154px;width:262px;font-size:10.4px;line-height:14.5px;text-align:justify;color:var(--white)}
.p4 .sub{left:86px;top:241px;font-size:13px;font-weight:700;color:var(--white)}
.p4 .ticks{left:64px;top:272px;width:262px;color:var(--white);font-size:10.4px;line-height:14.5px}
.p4 .ticks li{margin-bottom:13px}
.p4 .url{left:47px;width:293px;text-align:center;top:453px;color:var(--white)}

/* page 5 */
.p5{left:50px;top:777.5px;width:888px;height:499px;background:linear-gradient(135deg,#ffffff,#eceef1)}
.p5 .brand{left:28px;top:30px;color:var(--blue)}
.p5 h2{position:absolute;left:28px;top:68px;font-size:37px;line-height:38px;font-weight:800;color:var(--blue)}
.p5 h2 span{color:var(--grey)}
.p5 .body{left:31px;top:155px;width:370px;font-size:9.3px;line-height:13px;letter-spacing:-.15px}
.p5 .body p{margin-bottom:4px}
.p5 .chain{left:0;top:240px}
.step-label{position:absolute;font-size:12px;font-weight:600;color:var(--grey);transform:translateX(-50%);white-space:nowrap}
.p5 .url{left:31px;top:457px;color:#333}

/* page 6 */
.p6{left:619.5px;top:777.5px;width:884px;height:499px;background:linear-gradient(135deg,#ffffff,#eceef1)}
.p6 .brand{left:28px;top:30px;color:var(--blue)}
.p6 h2{position:absolute;right:44px;top:40px;font-size:28px;font-weight:800;color:var(--blue)}
.p6 h2 span{color:var(--grey)}
.p6 .subtitle{left:0;width:884px;top:90px;text-align:center;font-size:18.5px;line-height:25px;color:var(--blue)}
.col{position:absolute;top:312px}
.col h3{font-size:12.5px;font-weight:700;color:var(--blue);margin-bottom:10px;white-space:nowrap}
.col ul{font-size:9px;line-height:12px}
.col li{margin-bottom:5px;padding-left:12px}
.col li::before{left:0;top:4px;width:3px;height:3px}
.p6 .url{left:30px;top:457px;color:#333}
</style>
</head>
<body>

<svg width="0" height="0" style="position:absolute" aria-hidden="true">
  <defs>
    <marker id="head-blue" viewBox="0 0 10 10" refX="5" refY="5" markerWidth="2.2" markerHeight="2.2" orient="auto"><path d="M0 0L10 5L0 10Z" fill="var(--blue)"/></marker>
    <marker id="head-grey" viewBox="0 0 10 10" refX="5" refY="5" markerWidth="2.2" markerHeight="2.2" orient="auto"><path d="M0 0L10 5L0 10Z" fill="var(--arc-grey)"/></marker>
    <symbol id="icon-factory" viewBox="0 0 48 48"><path d="M6 42V16l10 8v-8l10 8V8h9v34Z" fill="none" stroke="currentColor" stroke-width="3" stroke-linejoin="round"/><path d="M13 36v-5M19 36v-5M25 36v-5M31 36v-5" stroke="currentColor" stroke-width="3"/></symbol>
    <symbol id="icon-cubes" viewBox="0 0 48 48"><g fill="none" stroke="currentColor" stroke-width="2.5" stroke-linejoin="round"><path d="M24 4l8 4.5v9L24 22l-8-4.5v-9Z"/><path d="M14 24l8 4.5v9L14 42l-8-4.5v-9Z"/><path d="M34 24l8 4.5v9L34 42l-8-4.5v-9Z"/></g></symbol>
    <symbol id="icon-database" viewBox="0 0 48 48"><g fill="none" stroke="currentColor" stroke-width="3"><ellipse cx="24" cy="11" rx="15" ry="5"/><path d="M9 11v26c0 3 7 5 15 5s15-2 15-5V11M9 20c0 3 7 5 15 5s15-2 15-5M9 29c0 3 7 5 15 5s15-2 15-5"/></g></symbol>
    <symbol id="icon-gear" viewBox="0 0 48 48"><g fill="none" stroke="currentColor"><circle cx="24" cy="24" r="15" stroke-width="6" stroke-dasharray="5 4.4"/><circle cx="24" cy="24" r="11" stroke-width="3"/><circle cx="24" cy="24" r="5" stroke-width="3"/></g></symbol>
    <symbol id="icon-tools" viewBox="0 0 48 48"><g fill="none" stroke="currentColor" stroke-width="3.5" stroke-linecap="round"><path d="M10 38L36 12"/><path d="M31 8l9 9"/><path d="M12 8l26 28"/><circle cx="11" cy="10" r="4"/><path d="M34 34l5 5"/></g></symbol>
    <symbol id="icon-chip" viewBox="0 0 48 48"><g fill="none" stroke="currentColor" stroke-width="2.5"><rect x="17" y="17" width="14" height="14" rx="2"/><circle cx="24" cy="24" r="3"/><path d="M24 17V9M24 31v8M17 24H9M31 24h8M19 19l-6-6M29 19l6-6M19 29l-6 6M29 29l6 6"/><circle cx="24" cy="6" r="2.5"/><circle cx="24" cy="42" r="2.5"/><circle cx="6" cy="24" r="2.5"/><circle cx="42" cy="24" r="2.5"/><circle cx="11" cy="11" r="2.5"/><circle cx="37" cy="11" r="2.5"/><circle cx="11" cy="37" r="2.5"/><circle cx="37" cy="37" r="2.5"/></g></symbol>
  </defs>
</svg>

<!-- Page 1 : cover -->
<section class="page p1">
  <svg class="abs" style="left:0;top:0" width="883" height="497" viewBox="0 0 883 497">
    <defs><radialGradient id="globe-glow" cx=".35" cy=".35" r=".7"><stop offset="0" stop-color="#5d8fd8" stop-opacity=".7"/><stop offset="1" stop-color="#0f2458" stop-opacity=".6"/></radialGradient></defs>
    <path d="M462 0Q360 250 462 497H883V0Z" fill="#6b6f75" role="img" aria-label="Black and white industrial photo collage: car showroom, driver at the wheel, bottling line"/>
    <path d="M462 0Q360 250 462 497" fill="none" stroke="#fff" stroke-width="6"/>
    <circle cx="745" cy="250" r="330" fill="#ffffff"/>
    <circle cx="745" cy="250" r="322" fill="#1b3f86" role="img" aria-label="Earth at night seen from space with glowing network lines"/>
    <circle cx="745" cy="250" r="322" fill="url(#globe-glow)"/>
  </svg>
  <div class="brand">NexaBRIDGE</div>
  <div class="abs tagline">WE HAVE A SOLUTION FOR<br><strong>ALL TYPES OF INDUSTRY.</strong></div>
  <ul class="abs ticks">
    <li>AUTOMOTIVE, CHEMICAL</li>
    <li>FOOD AND BEVERAGE</li>
    <li>MINING, PAPER AND PULP,</li>
    <li>OIL AND GAS, ENERGY MANAGEMENT</li>
  </ul>
  <div class="abs year">2021</div>
  <div class="abs rule"></div>
  <div class="url">www.nexabridge-mx.com</div>
</section>
<div class="page-label" style="left:55.5px;top:366px">PAGE 1</div>

<!-- Page 2 : key message -->
<section class="page p2">
  <svg class="abs" style="left:0;top:0" width="883" height="497" viewBox="0 0 883 497">
    <defs><linearGradient id="city" x1="0" y1="0" x2="0" y2="1"><stop offset="0" stop-color="#4f7f93"/><stop offset="1" stop-color="#163447"/></linearGradient></defs>
    <path d="M405 0H883V497H345L535 300Z" fill="url(#city)" role="img" aria-label="Blue toned city skyline with a tall art deco tower"/>
    <path d="M470 232L535 300L470 300Z" fill="none" stroke="#fff" stroke-width="4"/>
    <path d="M535 497L588 410L625 497Z" fill="#fff"/>
  </svg>
  <div class="abs key">KEY MESSAGE</div>
  <div class="brand">NexaBRIDGE</div>
  <div class="abs lead">Brochure to be delivered by our marketing process &amp; sales, This brochure will be deliverted to CEO´s worldwide in Industrial companies.</div>
  <ul class="abs dots">
    <li>Need to show in a few pages, what we can do for them:</li>
    <li>We offer product and projects to transform operations in manufacturing.</li>
    <li>Our work drives customers to Competitive Advantage Mode.</li>
    <li>We use Artificial Intelligence, Hyper Digitalization and Machine Learning</li>
    <li>Techniques to obtain cost reduction in Production Process, Better Quality Delivery,</li>
    <li>Asset &amp; Optimization Performance.</li>
    <li>We add productivity without changes into their actual operations in assetts</li>
  </ul>
  <div class="url">www.nexabridge-mx.com</div>
</section>
<div class="page-label" style="left:629px;top:366px">PAGE 2</div>

<!-- Page 3 : themes and benefits -->
<section class="page p3" role="img" aria-label="Port with cranes and container yard beneath a city skyline at sunset">
  <div class="brand">NexaBRIDGE</div>
  <div class="card themes">
    <div class="card-head">THEMES</div>
    <ul class="ticks">
      <li>We offer high performance technology</li>
      <li>State of the art in techniques with Artificial Intelligence and prototypes for new ways of doing manufacturing</li>
      <li>We play the rol as an Architect for a Digital world into the shopfloor operation at Machine Levels</li>
    </ul>
  </div>
  <div class="card terms">
    <div class="card-head">TERMS &amp; BENEFITS</div>
    <ul class="ticks">
      <li>Reduce cost operation in manufacturing in 30%</li>
      <li>Augmented Reality functions, adds 60% of productivity and efficiency at operator levels</li>
      <li>Save 17% in Energy for production</li>
      <li>Zero Unplanned Downtime in machine level</li>
      <li>Optimize consistency in recipes by 10% delivers 32% of cost reduction</li>
      <li>Supply Chain optimization by 1% of the cost of goods</li>
    </ul>
  </div>
  <div class="url">www.nexabridge-mx.com</div>
</section>
<div class="page-label" style="left:55.5px;top:735px">PAGE 3</div>

<!-- Page 4 : our DNA -->
<section class="page p4">
  <div class="abs strip"></div>
  <div class="abs" style="left:340px;top:0;width:543px;height:497px" role="img" aria-label="Hand reaching toward a glowing digital DNA helix in a starry dark space"></div>
  <div class="abs panel"></div>
  <div class="brand">NexaBRIDGE</div>
  <h2>OUR DNA</h2>
  <p class="abs intro">We want all companies to operate in an automated way, to be more efficient an dto compate with whoever is globally. We have the knwledge and experience to achive it.</p>
  <div class="abs sub">Our Commitments:</div>
  <ul class="abs ticks">
    <li>Improve the operation of each company individually.</li>
    <li>Impact the country's competitiveness</li>
    <li>Support Companies to access the highest levels of development, productivity, financing and profitability.</li>
  </ul>
  <div class="url">www.nexabridge-mx.com</div>
</section>
<div class="page-label" style="left:629px;top:735px">PAGE 4</div>

<!-- Page 5 : consulting strategy -->
<section class="page p5">
  <div class="abs" style="left:405px;top:25px;width:483px;height:195px;background:linear-gradient(135deg,#c9d3da,#8e9aa3 60%,#5f6b73)" role="img" aria-label="Two people working at a round table with laptops, coffee cup and a potted plant"></div>
  <div class="brand">NexaBRIDGE</div>
  <h2>CONSULTING<br><span>STRATEGY</span></h2>
  <div class="abs body">
    <p>We know that all customers are in different maturity level of digitalization.</p>
    <p>Our Strategy helps to start simple, low cost and produce big changes</p>
    <p>We have a graphic that represents the levels, and we need to show into a graph that we can help them to take positive path of optimization</p>
  </div>
  <svg class="abs chain" width="888" height="180" viewBox="0 240 888 180">
    <g fill="none" stroke-width="16">
      <path d="M67 330A66 66 0 0 1 193 322" stroke="var(--blue)" marker-end="url(#head-blue)"/>
      <path d="M189 330A66 66 0 0 0 315 338" stroke="var(--arc-grey)" marker-end="url(#head-grey)"/>
      <path d="M312 330A66 66 0 0 1 438 322" stroke="var(--blue)" marker-end="url(#head-blue)"/>
      <path d="M434 330A66 66 0 0 0 560 338" stroke="var(--arc-grey)" marker-end="url(#head-grey)"/>
      <path d="M556 330A66 66 0 0 1 682 322" stroke="var(--blue)" marker-end="url(#head-blue)"/>
      <path d="M679 330A66 66 0 0 0 805 322" stroke="var(--arc-grey)" marker-end="url(#head-grey)"/>
    </g>
    <g fill="#fff" stroke="#e3e6ea" stroke-width="2">
      <circle cx="133" cy="330" r="52"/><circle cx="255" cy="330" r="52"/><circle cx="378" cy="330" r="52"/>
      <circle cx="500" cy="330" r="52"/><circle cx="622" cy="330" r="52"/><circle cx="745" cy="330" r="52"/>
    </g>
    <g color="var(--blue)">
      <use href="#icon-factory" x="109" y="306" width="48" height="48"/>
      <use href="#icon-cubes" x="231" y="306" width="48" height="48"/>
      <use href="#icon-database" x="354" y="306" width="48" height="48"/>
      <use href="#icon-gear" x="476" y="306" width="48" height="48"/>
      <use href="#icon-tools" x="598" y="306" width="48" height="48"/>
      <use href="#icon-chip" x="721" y="306" width="48" height="48"/>
    </g>
  </svg>
  <div class="step-label" style="left:253px;top:248px">Interconnected</div>
  <div class="step-label" style="left:500px;top:248px">Automated</div>
  <div class="step-label" style="left:748px;top:248px">Manual Operations</div>
  <div class="step-label" style="left:133px;top:398px">Industry 4.0 IIOT</div>
  <div class="step-label" style="left:378px;top:398px">Storaging</div>
  <div class="step-label" style="left:622px;top:398px">Instrumented</div>
  <div class="url">www.nexabridge-mx.com</div>
</section>
<div class="page-label" style="left:54px;top:1094px;font-size:15px">Page 5</div>

<!-- Page 6 : maturity steps -->
<section class="page p6">
  <div class="brand">NexaBRIDGE</div>
  <h2>CONSULTING <span>STRATEGY</span></h2>
  <p class="abs subtitle">We analyse actual situation in operations We drive digital project to gain performance<br>Steps understanding the level of maturity</p>
  <svg class="abs" style="left:0;top:150px" width="884" height="160" viewBox="0 150 884 160">
    <g fill="none" stroke-width="16">
      <path d="M53 230A66 66 0 0 0 185 230" stroke="var(--arc-grey)"/>
      <path d="M55 232L53 220" stroke="var(--arc-grey)" marker-end="url(#head-grey)"/>
      <path d="M313 230A66 66 0 0 0 181 222" stroke="var(--blue)" marker-end="url(#head-blue)"/>
      <path d="M309 230A66 66 0 0 0 441 230" stroke="var(--arc-grey)"/>
      <path d="M568 230A66 66 0 0 0 437 222" stroke="var(--blue)" marker-end="url(#head-blue)"/>
      <path d="M567 230A66 66 0 0 0 699 230" stroke="var(--arc-grey)"/>
      <path d="M826 230A66 66 0 0 0 694 222" stroke="var(--blue)" marker-end="url(#head-blue)"/>
    </g>
    <g fill="#fff" stroke="#e3e6ea" stroke-width="2">
      <circle cx="119" cy="230" r="55"/><circle cx="247" cy="230" r="55"/><circle cx="375" cy="230" r="55"/>
      <circle cx="502" cy="230" r="55"/><circle cx="633" cy="230" r="55"/><circle cx="760" cy="230" r="55"/>
    </g>
    <g color="var(--blue)">
      <use href="#icon-chip" x="94" y="205" width="50" height="50"/>
      <use href="#icon-tools" x="222" y="205" width="50" height="50"/>
      <use href="#icon-gear" x="350" y="205" width="50" height="50"/>
      <use href="#icon-database" x="477" y="205" width="50" height="50"/>
      <use href="#icon-cubes" x="608" y="205" width="50" height="50"/>
      <use href="#icon-factory" x="735" y="205" width="50" height="50"/>
    </g>
  </svg>
  <div class="col" style="left:58px;width:130px"><h3>Manual Operations</h3><ul class="dots"><li>Partner ecosystem</li><li>Labor electrical &amp; mechanical Job by SI</li></ul></div>
  <div class="col" style="left:196px;width:126px"><h3>Instrumented</h3><ul class="dots"><li>HMI Low Cost</li><li>Manual Input</li><li>Workflow Instructions</li><li>Condition Base Monitoring</li></ul></div>
  <div class="col" style="left:330px;width:124px"><h3>Automated</h3><ul class="dots"><li>HMI SOADA Corvia</li><li>Augmented Reality</li><li>Industrial Digitalization</li><li>Workflow Prescriptive</li></ul></div>
  <div class="col" style="left:462px;width:106px"><h3>Storaging</h3><ul class="dots"><li>Historian</li><li>Other Sources noSQL Vexabase</li><li>BigData</li></ul></div>
  <div class="col" style="left:578px;width:122px"><h3>Interconnected</h3><ul class="dots"><li>API Rest. MQTT.</li><li>Web Services</li><li>ERP Connect</li><li>Cybersecurity</li></ul></div>
  <div class="col" style="left:708px;width:140px"><h3>Industry 4.0 IIOT</h3><ul class="dots"><li>Datascience</li><li>Analytics</li><li>Predictve &amp; Precriptive</li><li>Consulting Service</li></ul></div>
  <div class="url">www.nexabridge-mx.com</div>
</section>
<div class="page-label" style="left:619.5px;top:1094px;font-size:15px">Page 6</div>

</body>
</html>
```